wood grain ultrasonic essential oil aroma diffuser

Design a package that is simple but luxurious for the diffuser with my logo. My business is called “Open Petal Path”. The logo incorporates “Thoughts become things” the concept is positive thinking. I don’t particularly want the product featured as I have like to develop a uniform look for packaging and website and there are 2 different diffusers,

Target Market(s)

People interested in yoga, meditation, metaphysical aspects

Industry/Entity Type

Health And Wellness

Colors

Designer to choose colors to be used in the design.

Requirements
Must have
• Luxurious feel to packaging and alignment with the website

```html
<!DOCTYPE html>
<html lang="en">
<head>
<meta charset="utf-8">
<title>Open Petal Path — Essential Oil Aroma Diffuser Packaging</title>
<link rel="stylesheet" href="https://fonts.googleapis.com/css2?family=Montserrat:wght@400;600;700&display=swap">
<style>
  :root {
    --backdrop: #e6e6e6;
    --border-teal: #3d5b6a;
    --border-coral: #e98a78;
    --border-tan: #c8a77c;
    --panel-black: #050505;
    --panel-white: #f7f7f5;
    --ink-dark: #111111;
    --ink-light: #f2f2f2;
    --wood-dark: #2e241f;
    --wood-mid: #4a3a31;
    --glow: #3fd6d8;
  }
  * { margin: 0; padding: 0; box-sizing: border-box; }
  html, body { width: 1154px; height: 1200px; overflow: hidden; }
  body {
    background: var(--backdrop);
    font-family: "Montserrat", Arial, sans-serif;
    position: relative;
  }

  /* side panel */
  .side-panel {
    position: absolute; left: 60px; top: 80px; width: 140px; height: 1040px;
  }
  .side-border {
    position: absolute; inset: 0;
    background: linear-gradient(135deg, var(--border-teal), #4f7b82 50%, var(--border-coral));
  }
  .side-inner {
    position: absolute; left: 16px; right: 16px; top: 90px; bottom: 90px;
    background: var(--panel-black); color: var(--ink-light);
    padding: 18px 10px;
    display: flex; flex-direction: column; gap: 26px;
  }
  .side-title { font-size: 11px; font-weight: 600; line-height: 1.5; }
  .spec-list { list-style: none; display: flex; flex-direction: column; gap: 52px; }
  .spec-item { display: flex; align-items: center; gap: 8px; font-size: 9px; }
  .spec-item svg { flex: none; }

  /* front panel */
  .front-panel {
    position: absolute; left: 210px; top: 80px; width: 884px; height: 1040px;
  }
  .front-border {
    position: absolute; inset: 0;
    background: linear-gradient(135deg, var(--border-teal), #4f7b82 45%, var(--border-coral) 100%);
  }
  .frame-line {
    position: absolute; inset: 62px; border: 6px solid var(--border-tan);
  }
  .stripe-band {
    position: absolute; inset: 68px;
    background: linear-gradient(90deg, var(--border-coral), var(--border-tan), var(--border-teal));
  }
  .label-panel {
    position: absolute; left: 95px; top: 92px; width: 694px; height: 856px;
    background: var(--panel-black); overflow: hidden;
  }
  .wave { position: absolute; left: 0; top: 0; }
  .brand {
    position: absolute; left: 60px; top: 70px;
    display: flex; flex-direction: column; align-items: center; gap: 16px;
    width: 260px;
  }
  .brand-mark {
    width: 64px; height: 64px; border-radius: 50%; background: var(--ink-dark);
  }
  .brand-name {
    font-size: 22px; font-weight: 600; color: var(--ink-dark); letter-spacing: 0.5px;
  }
  .product-title {
    position: absolute; left: 0; right: 0; top: 312px;
    text-align: center; color: var(--ink-light); font-weight: 600;
  }
  .product-title .line-1 { font-size: 34px; letter-spacing: 5px; }
  .product-title .line-2 { font-size: 44px; letter-spacing: 5px; margin-top: 6px; }
  .product-visual {
    position: absolute; left: 130px; top: 460px; width: 434px; height: 360px;
    background: radial-gradient(ellipse at 50% 65%, var(--wood-mid), var(--wood-dark) 55%, var(--panel-black) 80%);
  }
</style>
</head>
<body>

<section class="side-panel">
  <div class="side-border" role="img" aria-label="Zigzag tribal border pattern in teal, coral and tan"></div>
  <div class="side-inner">
    <p class="side-title">Wood Grain Essential Oil<br>Ultrasonic Aroma Diffuser</p>
    <ul class="spec-list">
      <li class="spec-item"><svg width="14" height="20"><path d="M7 2v16" stroke="#f2f2f2" stroke-width="1.5"/></svg>Mist 25 ml/h</li>
      <li class="spec-item"><svg width="14" height="20"><rect x="3" y="2" width="8" height="16" fill="none" stroke="#f2f2f2" stroke-width="1.5"/></svg>Capacity 400 ml</li>
      <li class="spec-item"><svg width="14" height="20"><circle cx="7" cy="8" r="5" fill="none" stroke="#f2f2f2" stroke-width="1.5"/><path d="M5 15h4" stroke="#f2f2f2" stroke-width="1.5"/></svg>Seven colour lights</li>
      <li class="spec-item"><svg width="14" height="20"><rect x="2" y="2" width="10" height="16" rx="2" fill="none" stroke="#f2f2f2" stroke-width="1.5"/></svg>Timer 1/3/6 h</li>
      <li class="spec-item"><svg width="14" height="20"><circle cx="7" cy="10" r="5" fill="none" stroke="#f2f2f2" stroke-width="1.5"/></svg>Auto shut-off</li>
      <li class="spec-item"><svg width="14" height="20"><path d="M3 10h8M7 4v12" stroke="#f2f2f2" stroke-width="1.5"/></svg>Quiet 35 dB</li>
    </ul>
  </div>
</section>

<section class="front-panel">
  <div class="front-border" role="img" aria-label="Zigzag tribal border pattern in teal, coral and tan"></div>
  <div class="frame-line"></div>
  <div class="stripe-band" role="img" aria-label="Fine vertical stripe pattern in coral, tan and teal"></div>

  <div class="label-panel">
    <svg class="wave" width="694" height="260" viewBox="0 0 694 260">
      <path d="M0 0H694V20C620 40 560 70 470 120C360 185 260 225 150 222C90 220 40 205 0 190Z" fill="var(--panel-white)"/>
    </svg>
    <div class="brand">
      <div class="brand-mark"></div>
      <span class="brand-name">Open Petal Path</span>
    </div>
    <h1 class="product-title">
      <span class="line-1">ESSENTIAL OIL</span><br>
      <span class="line-2">AROMA DIFFUSER</span>
    </h1>
    <div class="product-visual" role="img" aria-label="Photograph of a dark wood grain tulip-shaped ultrasonic aroma diffuser with a glowing teal light ring"></div>
  </div>
</section>

</body>
</html>
```